Australian Trucking Company Requires Professional Looking Stationary

We require a professional looking stationary design that incorporates our newly designed logo.

Our business, called "Brell Haulage Contracting", provides contracting work, transport and logistics to business in Western Australia particularly with links to the mining sector.

We are a small business looking to expand and our new logo and our new stationary will help develop our brand image in our market place.

Target Market(s)

Businesses and Corporation with links to the Mining Sector

Industry/Entity Type

Small Business

Requirements
Must have
• The letterhead must have the following details:
The new logo

Text saying: "Brell Holdings Pty Ltd (ACN 582 316 907) ATF The Brell Discretionary Trust T/AS"
"ABN 71 834 209 553"
Address "P.O Box 817 Wattlegrove WA, 6958"
Phone: 08 9352 7140
Email: brellhaul@mailbox-example.com.au

The text on the letterhead should be editable as the details are likely to change in the near future. Provision should be made for a website address all though one isn't available at the moment.

The styling, layout and font text is entirely up to the designer.

```html
<!DOCTYPE html>
<html lang="en">
<head>
<meta charset="utf-8">
<title>Brell Haulage Contracting – Business Card</title>
<link rel="stylesheet" href="https://fonts.googleapis.com/css2?family=Open+Sans:wght@400;600;700&display=swap">
<style>
  :root {
    --bg: #e9e6e2;
    --card: #ffffff;
    --red: #e0232e;
    --red-dark: #b5121b;
    --ink: #3a3a3a;
    --ink-dark: #111111;
  }
  * { margin: 0; padding: 0; box-sizing: border-box; }
  html, body { width: 1200px; height: 426px; overflow: hidden; }
  body {
    background: var(--bg);
    font-family: "Open Sans", Arial, sans-serif;
    position: relative;
  }
  .card {
    position: absolute;
    top: 40px;
    width: 520px;
    height: 295px;
    background: var(--card);
    border-radius: 20px;
    overflow: hidden;
    box-shadow: 0 4px 12px rgba(0,0,0,0.18);
  }
  .card--front { left: 65px; }
  .card--back { left: 605px; }

  .band { position: absolute; }
  .band--top { top: 0; right: 0; width: 125px; height: 16px; }
  .band--bottom { left: 0; bottom: 0; width: 262px; height: 30px; }

  .brand {
    position: absolute;
    left: 150px;
    top: 36px;
    display: flex;
    align-items: center;
    gap: 12px;
  }
  .brand__mark {
    width: 18px; height: 18px;
    background: var(--red);
  }
  .brand__name {
    font-weight: 700;
    font-size: 27px;
    line-height: 30px;
    color: var(--red);
    text-transform: uppercase;
  }

  .person {
    position: absolute;
    left: 27px;
    top: 148px;
    font-size: 17px;
    font-weight: 700;
    color: var(--ink);
  }
  .person__role { font-size: 12px; font-weight: 400; }

  .contact {
    position: absolute;
    left: 22px;
    list-style: none;
    font-size: 12px;
    color: var(--ink-dark);
  }
  .contact--direct { top: 189px; }
  .contact--postal { top: 237px; }
  .contact li { display: flex; align-items: center; gap: 5px; height: 18px; }
  .contact svg { width: 11px; height: 11px; fill: var(--red); }

  .entity {
    position: absolute;
    right: 22px;
    top: 238px;
    width: 250px;
    text-align: center;
    font-size: 11.5px;
    line-height: 17px;
    color: var(--ink-dark);
  }

  .back-brand {
    position: absolute;
    inset: 0;
    display: flex;
    align-items: center;
    justify-content: center;
    font-weight: 700;
    font-size: 34px;
    color: var(--red);
    text-transform: uppercase;
    text-align: center;
    line-height: 40px;
  }
</style>
</head>
<body>

<section class="card card--front">
  <svg class="band band--top" viewBox="0 0 125 16" aria-hidden="true">
    <defs>
      <linearGradient id="bandTop" x1="0" x2="1">
        <stop offset="0" stop-color="#f03a44"/><stop offset="1" stop-color="#c4141d"/>
      </linearGradient>
    </defs>
    <polygon points="14,0 125,0 125,16 0,16" fill="url(#bandTop)"/>
  </svg>

  <div class="brand">
    <span class="brand__mark"></span>
    <span class="brand__name">Brell Haulage<br>Contracting</span>
  </div>

  <p class="person">Persons name, <span class="person__role">Manager</span></p>

  <ul class="contact contact--direct">
    <li>
      <svg viewBox="0 0 24 24" aria-hidden="true"><path d="M6.6 10.8a15.1 15.1 0 0 0 6.6 6.6l2.2-2.2c.3-.3.7-.4 1-.2 1.1.4 2.3.6 3.6.6.6 0 1 .4 1 1V20c0 .6-.4 1-1 1A17 17 0 0 1 3 4c0-.6.4-1 1-1h3.5c.6 0 1 .4 1 1 0 1.3.2 2.5.6 3.6.1.3 0 .7-.2 1z"/></svg>
      08 9352 7140
    </li>
    <li>
      <svg viewBox="0 0 24 24" aria-hidden="true"><path d="M2 5h20v14H2z M4 7v.5l8 5 8-5V7l-8 5z" fill-rule="evenodd"/></svg>
      brellhaul@mailbox-example.com.au
    </li>
  </ul>

  <ul class="contact contact--postal">
    <li>
      <svg viewBox="0 0 24 24" aria-hidden="true"><path d="M12 3 2 12h3v8h5v-5h4v5h5v-8h3z"/></svg>
      P.O Box 817 Wattlegrove WA, 6958
    </li>
  </ul>

  <p class="entity">
    Brell Holdings Pty Ltd (ACN 582 316 907)<br>
    ATF The Brell Discretionary Trust T/AS<br>
    ABN 71 834 209 553
  </p>

  <svg class="band band--bottom" viewBox="0 0 262 30" aria-hidden="true">
    <defs>
      <linearGradient id="bandBottom" x1="0" x2="1">
        <stop offset="0" stop-color="#c4141d"/><stop offset="1" stop-color="#f03a44"/>
      </linearGradient>
    </defs>
    <polygon points="0,0 240,0 262,30 0,30" fill="url(#bandBottom)"/>
  </svg>
</section>

<section class="card card--back">
  <p class="back-brand">Brell Haulage<br>Contracting</p>
</section>

</body>
</html>
```